4th Generation Family Business Needs a New Card Design!

We are a family owned 4th Generation company. We are based in the Sydney, Australia area and we are desperately in need of a more modern and classy card. We are monumental masons who design, supply & erect lasting memorials throughout cemeteries in Sydney. Our customers are normally in a period of grieving. I have attached logo files that will need to be implemented on the card. Company was established 1935. Australian Owned and Operated. Card needs to be designed to PIXO.com specification.

Target Market(s)

Our target market is based upon people that a grieving for family members that have passed away. We also deal with alot of companies that own and operate cemeteries.

Industry/Entity Type

Business

Contact Information for Business Card

Simon Harcourt, Operations Manager, 0417293086, simon@harcourtmemorials.com.au
Lewis Harcourt, Director, 0491630572, lewis@harcourtmemorials.com.au
Phone # 02 9561 3048
Website: www.harcourtmemorials.com.au
Address: Suite 17, 8 Palfrey Lane, West Carlow, Sydney NSW 2156

Font styles to use
Serif
Decorative
Script

Requirements
Must have
• Would like to see the logo nicely implemented with a modern design. Embossed lettering would be a nice additive.

```html
<!DOCTYPE html>
<html lang="en">
<head>
<meta charset="utf-8">
<title>Harcourt Memorials – Business Card</title>
<link rel="stylesheet" href="https://fonts.googleapis.com/css2?family=Cinzel:wght@600&family=Tinos&display=swap">
<style>
  :root {
    --backdrop: #e4e4e4;
    --card: #f7f7f7;
    --ink: #1c1c1c;
    --gold: #d6ad22;
    --band-dark: #141414;
    --rule: #d8d8d8;
    --paper-light: #ffffff;
  }
  * { margin: 0; padding: 0; box-sizing: border-box; }
  html, body {
    width: 1200px; height: 576px; overflow: hidden;
    background: var(--backdrop);
  }
  .sheet { position: relative; width: 1200px; height: 576px; }

  .card {
    position: absolute; top: 138px;
    width: 485px; height: 294px;
    background: linear-gradient(180deg, var(--paper-light) 0%, var(--card) 100%);
    overflow: hidden;
  }
  .card--front { left: 81px; }
  .card--back { left: 602px; }

  .brand-name {
    position: absolute; text-align: center;
    font-family: "Tinos", serif; font-weight: 400; color: var(--ink);
    line-height: 1.2;
  }
  .card--front .brand-name { left: 0; right: 0; top: 108px; font-size: 34px; }
  .card--back .brand-name { left: 20px; width: 176px; top: 108px; font-size: 24px; }

  .front-band {
    position: absolute; left: 0; right: 0; bottom: 0; height: 10px;
    background: var(--gold);
  }

  .divider {
    position: absolute; left: 210px; top: 62px; width: 1px; height: 144px;
    background: var(--rule);
  }

  .contact { position: absolute; left: 240px; top: 64px; color: var(--ink); font-family: "Tinos", serif; }
  .contact__name {
    font-family: "Cinzel", serif; font-weight: 600; font-size: 20px;
    letter-spacing: 0.5px; line-height: 1.1;
  }
  .contact__role { font-size: 12px; margin-top: 4px; }
  .contact__list { list-style: none; margin-top: 16px; font-size: 12.5px; }
  .contact__list li { display: flex; align-items: center; height: 17.5px; }
  .contact__list svg { width: 10px; height: 10px; margin-right: 12px; fill: var(--gold); }
  .contact__address { font-size: 12.5px; line-height: 18px; margin-top: 5px; }

  .back-band-gold {
    position: absolute; left: 0; bottom: 2px; width: 214px; height: 18px;
    background: var(--gold);
  }
  .back-band-dark { position: absolute; left: 200px; bottom: 0; width: 285px; height: 40px; }
  .website {
    position: absolute; left: 240px; bottom: 14px;
    font-family: "Tinos", serif; font-size: 12.5px; color: #f2f2f2; letter-spacing: 0.3px;
  }
</style>
</head>
<body>
<main class="sheet">
  <section class="card card--front" aria-label="Card front">
    <p class="brand-name">Harcourt<br>Memorials</p>
    <div class="front-band"></div>
  </section>

  <section class="card card--back" aria-label="Card back">
    <p class="brand-name">Harcourt<br>Memorials</p>
    <div class="divider"></div>

    <div class="contact">
      <h1 class="contact__name">Simon Harcourt</h1>
      <p class="contact__role">Operations Manager</p>
      <ul class="contact__list">
        <li>
          <svg viewBox="0 0 10 10" aria-hidden="true"><path d="M2 0.5 L3.6 2.6 L2.7 3.6 C3.3 5 4.9 6.6 6.4 7.3 L7.4 6.4 L9.5 8 L8.3 9.5 C4.5 9.2 0.8 5.5 0.5 1.7 Z"/></svg>
          0417293086
        </li>
        <li>
          <svg viewBox="0 0 10 10" aria-hidden="true"><path d="M0.5 3 C2.5 0.8 7.5 0.8 9.5 3 L8.5 4 L7 3.2 L7 2.6 C5.7 2.2 4.3 2.2 3 2.6 L3 3.2 L1.5 4 Z M2.5 4.8 L7.5 4.8 L9 9 L1 9 Z"/></svg>
          02 9561 3048
        </li>
        <li>
          <svg viewBox="0 0 10 10" aria-hidden="true"><path d="M0.5 2 L9.5 2 L5 5.5 Z M0.5 3 L5 6.5 L9.5 3 L9.5 8.5 L0.5 8.5 Z"/></svg>
          simon@harcourtmemorials.com.au
        </li>
      </ul>
      <p class="contact__address">Suite 17, 8 Palfrey Lane,<br>West Carlow, Sydney NSW 2156</p>
    </div>

    <div class="back-band-gold"></div>
    <svg class="back-band-dark" viewBox="0 0 285 40" preserveAspectRatio="none" aria-hidden="true">
      <polygon points="22,0 285,0 285,40 0,40" fill="var(--band-dark)"/>
    </svg>
    <p class="website">www.harcourtmemorials.com.au</p>
  </section>
</main>
</body>
</html>
```